Music Producer Website

I need a website designed for my music production company. We specialize in finding talented musicians and matching them with music producers all over the United States. A visitor can create a profile and/or upload their music demo and we submit it to thousands of music producers and production companies for review. In many cases, our members will receive multiple signing offers from music producers allowing them to choose the contract that is best for them. "We turn aspiring musicians into SuperStars!"
Please include photos that reflect all genres of music (black artists, white artists, both male and female.) We produce all types of music including rap, R&B, rock, country, and Hip Hop.
When a user creates a profile, they become visible to thousands of record producers who are looking to sign new talent and make them stars.
Somewhere in the top half of the page, please include a small form that the visitor can fill out. The form should look as follows:
Title (large and bold): Contact Us or Submit Music Demo
Fields to include (* = required): First Name*, Last Name*, Age, Zip Code, Email Address*, Daytime Phone, Evening Phone, Comments
Then, there will be a "submit" button to proceed to next step of form. Just below the "submit" button, should be the following verbiage: "After submitting, you will have the opportunity to upload demos of your music (optional) and provide other pertinent information about yourself, band, or group."
Updates
Reason: I have not seen a design that I am 100% satisfied with yet. Ideally, rotating header images (GIF or other) with several different music producers in studio (male, female, black, white) would be perfect. Here are some examples of how the header pics could look:
http://files.quillmarsh.net/art_img/514302/806421/806421_7391046_514302_image.jpg
http://files.quillmarsh.net/art_img/514302/806421/806421_7391058_514302_image.jpg
http://files.quillmarsh.net/art_img/514302/806421/806421_7391037_514302_image.jpg
Also, there should be a form on the site (somewhere in upper half of the page) with the following headline:
GET FOUND AND BECOME A STAR! (super large, super-bold font)
Contact Us or Submit Your Music for Review (large font, not as bold as headline)
First Name
Last Name
Age
Zip Code
Email Address
Daytime Phone
Evening Phone
Comments
Target Market(s)
We are targeting all types of musicians including rock, rap, pop, R&B, country, gospel, etc.
Industry/Entity Type
Artists
Colors
Designer to choose colors to be used in the design.
Look and feel
Each slider illustrates characteristics of the customer's brand and the style your logo design should communicate.

```html
<!DOCTYPE html>
<html lang="en">
<head>
<meta charset="utf-8">
<title>Vireo Music Productions</title>
<link href="https://fonts.googleapis.com/css2?family=Lato:wght@300;400;700;900&display=swap" rel="stylesheet">
<style>
:root{
  --black:#000;
  --ink:#0b0b0c;
  --gold:#b5a67c;
  --white:#fff;
  --muted:#8a8170;
  --field:#fff;
  --sand:#e9dfd4;
  --red:#c2412a;
  --stage-blue:#3f63c4;
  --stage-deep:#0c1238;
  --map-tan:#cdb897;
  --map-brown:#9c7a52;
  --map-pale:#e4dccf;
}
*{box-sizing:border-box;margin:0;padding:0}
html,body{width:1200px;height:2261px;overflow:hidden;background:var(--black)}
body{position:relative;font-family:'Lato',sans-serif;color:var(--white)}
.abs{position:absolute}

/* hero */
.hero-photo{left:0;top:0;width:1200px;height:944px;
  background:
    radial-gradient(ellipse 260px 200px at 560px 300px,rgba(190,215,255,.85) 0%,rgba(120,160,240,.35) 55%,rgba(0,0,0,0) 100%),
    radial-gradient(ellipse 180px 260px at 230px 330px,rgba(235,205,170,.55) 0%,rgba(0,0,0,0) 100%),
    radial-gradient(ellipse 200px 300px at 420px 380px,rgba(225,190,160,.45) 0%,rgba(0,0,0,0) 100%),
    radial-gradient(ellipse 160px 320px at 620px 400px,rgba(60,60,70,.7) 0%,rgba(0,0,0,0) 100%),
    radial-gradient(ellipse 300px 120px at 320px 470px,rgba(190,80,40,.45) 0%,rgba(0,0,0,0) 100%),
    radial-gradient(ellipse 220px 420px at 1080px 200px,rgba(30,50,140,.9) 0%,rgba(0,0,0,0) 100%),
    linear-gradient(180deg,rgba(0,0,0,0) 0%,rgba(0,0,0,0) 52%,rgba(10,20,70,.6) 62%,rgba(20,40,120,.55) 75%,rgba(4,6,20,.9) 100%),
    radial-gradient(ellipse at 50% 35%,#6a8ee0 0%,var(--stage-blue) 28%,#1c2c78 55%,var(--stage-deep) 80%,#04050f 100%)}
.site-header{left:119px;top:0;width:959px;height:122px;background:rgba(0,0,0,.85)}
.brand{left:34px;top:36px;font-weight:700;color:var(--gold);line-height:1}
.brand-name{font-size:42px;letter-spacing:2px;display:block}
.brand-sub{font-size:12px;letter-spacing:1px;display:block;margin-top:4px}
.account-link{left:655px;top:26px;font-size:14px}
.social{top:21px;width:26px;height:26px;border-radius:50%}
.search{left:916px;top:20px;width:28px;height:28px;border-radius:50%;background:var(--gold)}
.main-nav{font-size:16px;font-weight:700}
.main-nav span{position:absolute;white-space:nowrap}
.main-nav em{font-style:normal;color:var(--gold)}
.nav-active{left:384px;top:66px;width:100px;height:3px;background:var(--gold)}
.slide-arrow{top:276px}
.superstar-band{left:640px;top:377px;width:434px;height:90px;background:rgba(0,0,0,.7)}
.tag-small{left:697px;top:335px;width:374px;height:38px;background:rgba(232,232,232,.94);color:#111;
  font-size:26px;font-weight:700;text-align:center;line-height:38px}
.tag-big{left:688px;top:377px;width:386px;height:90px;color:var(--white);
  font-size:72px;font-weight:700;text-align:center;line-height:90px}

/* signup form */
.signup{left:77px;top:537px;width:1059px;height:405px;background:rgba(0,0,0,.86)}
.signup-kicker{left:46px;top:20px;font-size:42px;font-weight:900;line-height:1}
.signup-title{left:44px;top:58px;font-size:74px;font-weight:900;color:var(--gold);line-height:1;letter-spacing:1px}
.field{background:var(--field);height:30px;color:#9a9a9a;font-size:15px;padding:6px 10px}
.req{color:var(--white);font-size:12px}
.artist-photo{left:733px;top:78px;width:268px;height:218px;
  background:
    radial-gradient(ellipse 70px 90px at 120px 95px,rgba(220,220,220,.9) 0%,rgba(120,120,120,.5) 60%,rgba(0,0,0,0) 100%),
    radial-gradient(ellipse 130px 90px at 150px 190px,rgba(150,150,150,.55) 0%,rgba(0,0,0,0) 100%),
    radial-gradient(ellipse at 50% 50%,#4a4a4a 0%,#1c1c1c 55%,rgba(0,0,0,0) 85%)}
.submit{left:695px;top:299px;width:306px;height:44px;background:var(--gold);color:var(--white);
  font-size:30px;font-weight:700;text-align:center;line-height:44px}
.signup-note{left:0;top:362px;width:1059px;text-align:center;font-size:13px;color:var(--muted)}

/* welcome */
.welcome{left:0;top:944px;width:1200px;height:375px;
  background:
    radial-gradient(ellipse 140px 260px at 700px 260px,rgba(20,14,8,.85) 0%,rgba(0,0,0,0) 100%),
    radial-gradient(ellipse 420px 220px at 720px 90px,rgba(205,160,100,.55) 0%,rgba(0,0,0,0) 100%),
    linear-gradient(180deg,rgba(0,0,0,0) 55%,rgba(8,6,4,.75) 100%),
    radial-gradient(ellipse at 65% 35%,#8e6a3e 0%,#5a3f22 30%,#24190e 65%,#0e0905 100%)}
.welcome-title{left:160px;top:88px;font-size:74px;font-weight:700;line-height:88px}
.welcome-title .gold{color:var(--gold)}
.welcome-copy{left:527px;top:68px;width:553px;font-size:13.5px;line-height:17.7px;color:#eee}
.welcome-copy p+p{margin-top:17.7px}

/* testimonial */
.testimonial{left:0;top:1319px;width:1200px;height:301px;background:var(--black)}
.quote-line{left:122px;top:89px;width:956px;height:1px;background:#555}
.quote-text{left:0;top:131px;width:1200px;text-align:center;font-size:23px;font-weight:300;color:#c9c9c9;line-height:29px}
.quote-author{left:0;top:226px;width:1200px;text-align:center;font-size:16px;font-weight:700}
.quote-author em{font-style:normal;color:var(--gold)}
.dot{width:11px;height:11px;border-radius:50%;background:var(--gold)}
.dot.on{background:var(--red)}

/* concerts */
.concerts{left:0;top:1620px;width:1200px;height:468px}
.sand{left:0;top:0;width:119px;height:468px;background:var(--sand)}
.schedule{left:119px;top:0;width:388px;height:468px;background:var(--ink)}
.schedule-title{left:0;top:8px;width:388px;text-align:center;font-size:64px;font-weight:700;line-height:56px}
.schedule-title .gold{color:var(--gold)}
.next-bar{left:0;top:138px;width:388px;height:62px;background:var(--gold);font-size:27px;font-weight:700;line-height:62px;padding-left:28px}
.event-date{left:32px;font-size:16px;font-weight:700}
.event-place{left:32px;font-size:20px;font-weight:700;color:var(--gold);line-height:26px}
.event-rule{left:0;top:343px;width:388px;height:1px;background:#3a3a3a}
.map{left:507px;top:0;width:693px;height:468px;
  background:
    radial-gradient(ellipse 150px 90px at 330px 250px,rgba(228,220,207,.95) 0%,rgba(228,220,207,0) 100%),
    radial-gradient(ellipse 120px 70px at 560px 320px,rgba(228,220,207,.8) 0%,rgba(228,220,207,0) 100%),
    radial-gradient(ellipse 140px 110px at 120px 120px,rgba(156,122,82,.75) 0%,rgba(156,122,82,0) 100%),
    radial-gradient(ellipse 170px 90px at 470px 90px,rgba(156,122,82,.7) 0%,rgba(156,122,82,0) 100%),
    radial-gradient(ellipse 130px 120px at 560px 420px,rgba(156,122,82,.6) 0%,rgba(156,122,82,0) 100%),
    radial-gradient(ellipse 110px 80px at 90px 380px,rgba(200,190,175,.9) 0%,rgba(200,190,175,0) 100%),
    linear-gradient(135deg,var(--map-tan) 0%,#bda27d 45%,var(--map-pale) 100%)}
.map-pin{width:43px;height:52px;background:#1d1d1d;border:1px solid #777;color:var(--white);text-align:center;font-size:12px;font-weight:700;line-height:14px;padding-top:4px}
.map-pin small{display:block;font-size:9px;font-weight:400}

/* footer */
.site-footer{left:0;top:2088px;width:1200px;height:173px;background:var(--black)}
.footer-brand{left:0;top:44px;width:1200px;text-align:center;font-size:36px;font-weight:700;color:var(--gold);letter-spacing:2px;line-height:1}
.footer-copy{left:0;top:111px;width:1200px;text-align:center;font-size:12px}
.footer-links{left:0;top:136px;width:1200px;text-align:center;font-size:12px}
</style>
</head>
<body>

<div class="abs hero-photo" role="img" aria-label="Band of three performing on a lit concert stage before a large crowd"></div>

<header class="abs site-header">
  <div class="abs brand"><span class="brand-name">VIREO</span><span class="brand-sub">Music Productions</span></div>
  <div class="abs account-link">login / register</div>
  <div class="abs social" style="left:789px;background:#3b5b98"></div>
  <div class="abs social" style="left:821px;background:#3aa0dd"></div>
  <div class="abs social" style="left:855px;background:#d6392d"></div>
  <div class="abs search">
    <svg width="28" height="28" viewBox="0 0 28 28"><circle cx="12.5" cy="12.5" r="5" fill="none" stroke="#fff" stroke-width="2"/><line x1="16" y1="16" x2="20" y2="20" stroke="#fff" stroke-width="2.5" stroke-linecap="round"/></svg>
  </div>
  <div class="abs nav-active"></div>
  <nav class="abs main-nav" style="left:0;top:84px">
    <span style="left:386px">About <em>Vireo</em></span>
    <span style="left:538px">Team <em>Vireo</em></span>
    <span style="left:684px">Join <em>Vireo</em></span>
    <span style="left:814px">Contact <em>Vireo</em></span>
  </nav>
</header>

<svg class="abs slide-arrow" style="left:36px" width="20" height="32" viewBox="0 0 20 32"><polyline points="15,4 4,16 15,28" fill="none" stroke="#fff" stroke-width="4"/></svg>
<svg class="abs slide-arrow" style="left:1141px" width="20" height="32" viewBox="0 0 20 32"><polyline points="5,4 16,16 5,28" fill="none" stroke="#fff" stroke-width="4"/></svg>

<div class="abs superstar-band"></div>
<div class="abs tag-small">We turn aspiring musicians into</div>
<div class="abs tag-big">SuperStars!</div>

<section class="abs signup">
  <div class="abs signup-kicker">GET FOUND AND</div>
  <div class="abs signup-title">BECOME A STAR!</div>

  <div class="abs field" style="left:44px;top:137px;width:307px">First name</div>
  <span class="abs req" style="left:354px;top:128px">*</span>
  <div class="abs field" style="left:369px;top:137px;width:306px">Last name</div>
  <span class="abs req" style="left:678px;top:128px">*</span>

  <div class="abs field" style="left:44px;top:183px;width:141px">Age</div>
  <div class="abs field" style="left:207px;top:183px;width:144px">Zip Code</div>
  <div class="abs field" style="left:369px;top:183px;width:306px">Email Address</div>
  <span class="abs req" style="left:678px;top:174px">*</span>

  <div class="abs field" style="left:44px;top:226px;width:307px">Daytime Phone</div>
  <div class="abs field" style="left:369px;top:226px;width:306px">Evening Phone</div>

  <div class="abs field" style="left:44px;top:267px;width:631px;height:76px">Comments</div>

  <div class="abs artist-photo" role="img" aria-label="Young artist in sunglasses wearing headphones, black and white"></div>
  <div class="abs submit">SUBMIT</div>
  <p class="abs signup-note">After submitting, you will have the opportunity to upload demos of your music (optional) and provide other pertinent information about yourself, band, or group.</p>
</section>

<section class="abs welcome" role="img" aria-label="Guitarist silhouetted on a warmly lit stage">
  <h2 class="abs welcome-title">Welcome<br><span class="gold">to Vireo</span></h2>
  <div class="abs welcome-copy">
    <p>Lorem ipsum dolor sit amet, consectetur adipiscing elit. Sed adipiscing sit amet sem sit amet viverra. Cras porta justo risus, quis sodales diam placerat vitae. Quisque eget dui orci. Cras aliquet, odio quis gravida fermentum, nibh lorem vulputate nunc, ut condimentum mauris ipsum non ipsum. Duis eleifend mauris nibh, ac hendrerit nisi bibendum dignissim. Nullam blandit urna vulputate nisl dignissim, vel tempus ante porttitor. Sed sed mi ac eros viverra rhoncus. Sed tempor sodales libero sit amet convallis.</p>
    <p>Morbi ac lectus lectus. Proin vitae facilisis enim. Suspendisse a fermentum magna. Curabitur accumsan ac magna ac vehicula. Sed sollicitudin, magna sed commodo pretium, arcu nunc tincidunt sem, quis laoreet felis eros et arcu. Maecenas porta tempus vulputate. Sed iaculis orci adipiscing lectus molestie dapibus. In vehicula, libero sit amet dapibus luctus, felis massa tincidunt eros, sodales fringilla lorem sem nec diam.</p>
  </div>
</section>

<section class="abs testimonial">
  <div class="abs quote-line"></div>
  <svg class="abs" style="left:553px;top:42px" width="92" height="48" viewBox="0 0 92 48">
    <path d="M1 47.5 A45 45 0 0 1 91 47.5" fill="#000" stroke="#555" stroke-width="1.5"/>
    <text x="46" y="64" text-anchor="middle" font-family="Lato,sans-serif" font-weight="900" font-size="72" fill="#fff">&#8220;</text>
  </svg>
  <p class="abs quote-text">" Lorem ipsum dolor sit amet, consectetur adipiscing elit. In imperdiet diam augue,<br>vitae lacinia leo lacinia sit amet. Nulla facilisi. Cras cursus sed odio a mollis"</p>
  <p class="abs quote-author">Jordan Hale&nbsp; <em>producers</em></p>
  <div class="abs dot on" style="left:567px;top:276px"></div>
  <div class="abs dot" style="left:584px;top:276px"></div>
  <div class="abs dot" style="left:601px;top:276px"></div>
</section>

<section class="abs concerts">
  <div class="abs sand"></div>
  <div class="abs schedule">
    <h2 class="abs schedule-title">Concert<br><span class="gold">schedule</span></h2>
    <div class="abs next-bar">NEXT CONCERT
      <svg class="abs" style="left:326px;top:14px" width="34" height="34" viewBox="0 0 34 34" fill="#fff">
        <rect x="2" y="5" width="30" height="27" fill="none" stroke="#fff" stroke-width="2.5"/>
        <rect x="2" y="5" width="30" height="6"/>
        <rect x="8" y="1" width="3" height="7"/><rect x="23" y="1" width="3" height="7"/>
        <rect x="7" y="15" width="5" height="4"/><rect x="15" y="15" width="5" height="4"/><rect x="23" y="15" width="5" height="4"/>
        <rect x="7" y="23" width="5" height="4"/><rect x="15" y="23" width="5" height="4"/><rect x="23" y="23" width="5" height="4"/>
      </svg>
    </div>
    <div class="abs dot on" style="left:174px;top:218px"></div>
    <div class="abs dot" style="left:191px;top:218px"></div>
    <div class="abs dot" style="left:208px;top:218px"></div>
    <div class="abs event-date" style="top:244px">2 November 2013</div>
    <div class="abs event-place" style="top:281px">Harbor Light Arena - 2040 Alder Row,<br>Los Angeles, CA, US</div>
    <div class="abs event-rule"></div>
    <div class="abs event-date" style="top:365px">10 November 2013</div>
    <div class="abs event-place" style="top:402px">Harbor Light Arena - 2040 Alder Row,<br>Los Angeles, CA, US</div>
  </div>
  <div class="abs map" role="img" aria-label="Terrain map of the southwestern United States showing concert locations">
    <div class="abs map-pin" style="left:205px;top:155px">10<br>Nov<small>2013</small></div>
    <div class="abs map-pin" style="left:92px;top:245px">2<br>Nov<small>2013</small></div>
  </div>
</section>

<footer class="abs site-footer">
  <div class="abs footer-brand">VIREO</div>
  <p class="abs footer-copy">Copyright 2013 © Music Producers.</p>
  <p class="abs footer-links">Privacy Policy | Terms and Conditions | Site Map | Feedback | Report Bug | Contact Us</p>
</footer>

</body>
</html>
```